Letterhead Design Project

Brightfern Consulting is a newly created boutique consultancy focussing on delivering strategic consulting to medium and large businesses, with a focus on:
- Strategic planning and execution.
- Corporate function optimisation, especially in the areas of finance, commercial, and IT. This includes implementing the right functional design for the needs of the business, and ensuring the right skills.
- Performance management, in particular project governance and control, operational metrics and management reporting.
I have in mind a tag line for the business being:
"Helping business to discover sustainable value."
I am looking for a letterhead design which utilises my new logo on report templates (powerpoint and word), and letterhead.
Knowlopedia defines a mother lode as follows:
"Mother lode is a principal vein or zone of veins of gold or silver ore. The term probably came from a literal translation of the Spanish veta madre, a term common in old Mexican mining. Veta madre, for instance, is the name given to an 11-kilometre-long (6.8 mi) silver vein discovered in 1548 in Guanajuato, New Spain (modern-day Mexico)."
My preference is for black and gold. Logo files are attached in .eps format. All fonts are outlined. The fonts that are used are "Crimson Text" and "Josefin Sans". They are free open source fonts and they are available here: http://www.typevault-example.com/fonts
Target Market(s)
Medium to large corporates.
Industry/Entity Type
Boutique
Font styles to use
Other font styles liked:
- All fonts are outlined. The fonts that are used are "Crimson Text" and "Josefin Sans". They are free open source fonts and they are available here: http://www.typevault-example.com/fonts
Look and feel
Each slider illustrates characteristics of the customer's brand and the style your logo design should communicate.

```html
<!DOCTYPE html>
<html lang="en">
<head>
<meta charset="utf-8">
<title>Brightfern Consulting — Letterhead</title>
<link rel="stylesheet" href="https://fonts.googleapis.com/css2?family=Crimson+Text:wght@400&display=swap">
<style>
  :root {
    --backdrop: #e9e6e1;
    --paper: #ffffff;
    --ink: #111111;
    --band-dark: #0c0c0c;
    --band-mid: #2b2b2b;
    --gold: #c9992a;
    --rule-gold: #e0b23a;
  }
  * { margin: 0; padding: 0; box-sizing: border-box; }
  html, body {
    width: 1200px;
    height: 899px;
    overflow: hidden;
    background: var(--backdrop);
  }
  .letterhead {
    position: absolute;
    left: 303px;
    top: 40px;
    width: 613px;
    height: 792px;
    background: var(--paper);
    box-shadow: 0 1px 6px rgba(0, 0, 0, 0.18);
    font-family: "Crimson Text", Georgia, serif;
    color: var(--ink);
  }
  .header-band {
    position: absolute;
    left: 0;
    top: 0;
    width: 613px;
    height: 60px;
    background: linear-gradient(180deg, var(--band-dark) 0%, var(--band-mid) 75%, var(--gold) 100%);
  }
  .brand {
    position: absolute;
    left: 22px;
    top: 78px;
    display: flex;
    align-items: center;
    gap: 8px;
  }
  .brand-square {
    width: 52px;
    height: 52px;
    border: 4px solid var(--ink);
  }
  .brand-name {
    font-size: 22px;
    line-height: 1.05;
    letter-spacing: 0.5px;
    text-transform: uppercase;
    color: var(--ink);
  }
  .footer-tagline {
    position: absolute;
    left: 0;
    right: 0;
    top: 741px;
    line-height: 16px;
    text-align: center;
    font-size: 11px;
    letter-spacing: 1.2px;
    text-transform: uppercase;
  }
  .footer-rule-gold {
    position: absolute;
    left: 38px;
    width: 537px;
    top: 760px;
    height: 1.5px;
    background: var(--rule-gold);
  }
  .footer-rule-black {
    position: absolute;
    left: 11px;
    width: 591px;
    top: 765px;
    height: 1px;
    background: var(--ink);
  }
  .footer-contact {
    position: absolute;
    left: 0;
    right: 0;
    top: 772px;
    line-height: 14px;
    text-align: center;
    font-size: 9.5px;
    letter-spacing: 0.8px;
    text-transform: uppercase;
    word-spacing: 1px;
  }
  .footer-contact .phone { margin-left: 20px; }
  .footer-contact .fax { margin-left: 10px; }
</style>
</head>
<body>
  <main class="letterhead">
    <div class="header-band" role="img" aria-label="Decorative black and gold curved header band"></div>

    <div class="brand">
      <div class="brand-square"></div>
      <div class="brand-name">Brightfern<br>Consulting</div>
    </div>

    <footer>
      <p class="footer-tagline">"Helping business to discover sustainable value."</p>
      <div class="footer-rule-gold"></div>
      <div class="footer-rule-black"></div>
      <p class="footer-contact">
        <span class="address">000 XYZ Lane, City, Postal Code</span><span class="phone">P: (000) 000-000</span><span class="fax">F: (000) 000-000</span>
      </p>
    </footer>
  </main>
</body>
</html>
```